Anzeigengestaltung für eine Hausarztpraxis
Zielgruppe
Wir sind eine Hausarztpraxis mit zwei Standorten und suchen eine Ärztin oder einen Arzt zur Anstellung in der klassischen Hausarzt Medizin am Standort Erlenbrunn
Aufgabenstellung
Bitte beachtet den Text im Anhang, der ist schon vorgegeben. (Anzeigentext)
Wir suchen ein ruhiges, hochwertiges Layout für eine Stellenanzeige einer Hausarztpraxis in einem historischen Gebäude.
Der Text steht im Vordergrund, das Design soll zurückhaltend, klar und wertig sein.
Bitte keine Icons, keine bunten Farben, keine verspielten Elemente.
Gerne viel Weissraum, klare Typografie, ruhige Anmutung.
Schrift: Garamond für den Fliesstext (bereits gewählt).
Das Layout soll sowohl als PDF wie auch online funktionieren.
Optional: ein sehr dezentes grafisches Element oder eine ruhige Bildanmutung (z. B. Struktur, Licht, Architekturdetail).

```html
<!DOCTYPE html>
<html lang="de">
<head>
<meta charset="utf-8">
<title>Stellenanzeige Hausarztpraxis Erlenbrunn</title>
<link href="https://fonts.googleapis.com/css2?family=Open+Sans:ital,wght@0,400;0,600;0,700;1,400&display=swap" rel="stylesheet">
<style>
  :root {
    --backdrop: #e9e8e5;
    --paper: #ffffff;
    --ink: #3b3b3b;
    --ink-soft: #4a4a4a;
    --accent: #84bd32;
  }
  * { margin: 0; padding: 0; box-sizing: border-box; }
  html, body {
    width: 1200px; height: 2396px; overflow: hidden;
    background: var(--backdrop);
    font-family: "Open Sans", sans-serif;
    color: var(--ink);
  }
  .ad-page {
    position: absolute; left: 50px; top: 420px;
    width: 1100px; height: 1555px;
    background: var(--paper);
    box-shadow: 0 10px 40px rgba(0,0,0,0.12);
  }
  .ad-page > * { position: absolute; }
  .headline {
    left: 116px; top: 96px; width: 900px;
    font-size: 45px; line-height: 62px; font-weight: 600; color: var(--ink);
  }
  .headline em { font-style: italic; font-weight: 400; color: var(--ink-soft); }
  .intro { left: 116px; top: 252px; width: 900px; font-size: 18.5px; line-height: 34px; white-space: nowrap; }
  .intro em { display: block; font-size: 22px; }
  .body-text { font-size: 14.5px; line-height: 29.5px; color: var(--ink); }
  .col-left { left: 116px; width: 370px; }
  .col-right { left: 604px; width: 370px; }
  .section-title {
    font-size: 26px; font-weight: 400; line-height: 34px; color: var(--ink);
    padding-bottom: 6px; border-bottom: 2px solid var(--accent); width: 312px;
  }
  .section-title + .body-text { margin-top: 30px; }
  .closing {
    left: 116px; top: 1202px; width: 880px;
    font-size: 18px; line-height: 33px; font-style: italic;
  }
  .practice-name {
    left: 116px; top: 1418px;
    display: flex; align-items: center; gap: 10px;
    font-size: 15px; font-weight: 600; color: var(--ink);
  }
  .practice-name .dot { width: 12px; height: 12px; border-radius: 50%; background: var(--accent); }
  .contact { left: 604px; top: 1388px; font-size: 19px; line-height: 26px; font-style: normal; }
  .contact .email { font-weight: 700; }
</style>
</head>
<body>
  <article class="ad-page">
    <h1 class="headline">Hausarztmedizin mit Tiefe&nbsp; <em>dort, wo<br>man noch echte Grundversorgung lebt</em></h1>

    <p class="intro"><em>Ein Ort, der trägt. Ein Team, das bleibt. Eine Arbeit, die Wertschätzung hat.</em>
      Manche Orte verändern die Art, wie man arbeitet. Unsere Praxis in Erlenbrunn ist so ein Ort.</p>

    <p class="body-text col-left" style="top:440px">In einem historischen Gebäude gelegen, mit grosszügigem Ambiente, warmen Vertäfelungen und kunstvoller Wandbemalung, entstehen hier Behand­lungsräume von Ruhe und Würde. Kein steriler Praxisalltag, sondern ein Ort, der Gespräche trägt und medizinische Arbeit unterstützt.</p>

    <p class="body-text col-left" style="top:691px">Für diesen besonderen Ort suchen wir eine Hausärz­tin oder einen Hausarzt, die oder der nicht einfach einen Arbeitsplatz sucht, sondern einen Platz, an dem Medizin menschlich sein darf.</p>

    <section class="col-right" style="top:444px">
      <h2 class="section-title">Zeit für gute Medizin</h2>
      <p class="body-text">Unsere Patientinnen und Patienten sind überwieg­end gut bis sehr gut situiert, wertschätzend und therapieoffen. Das ermöglicht ruhiges, strukturiertes Arbeiten mit Fokus auf Qualität, Beziehung und nachhaltige Behandlung.</p>
    </section>

    <section class="col-right" style="top:773px">
      <h2 class="section-title">Und sonst?</h2>
      <p class="body-text">Der Praxisalltag ist klar strukturiert, ruhig und verlässlich. Geregelte und in Abstimmung flexible Arbeitszeiten ohne Wochenend- oder Nachtdienste, eine sehr gute leistungsbezogene Vergütung sowie ein respektvoller, wertschätzender Umgang auf Augenhöhe schaffen ein Umfeld, in dem man sich auf die medizinische Arbeit konzentrieren und langfristig wohlfühlen kann.</p>
    </section>

    <section class="col-left" style="top:926px">
      <h2 class="section-title">Ein Team mit Haltung</h2>
      <p class="body-text">Sie arbeiten in einem freundlichen, über Jahre gewachsenen Team mit hoher personeller Kontinu­ität und geringer Fluktuation.</p>
    </section>

    <p class="closing">Wir freuen uns über eine unkomplizierte Kontaktaufnahme per E-Mail oder Telefon – gerne auch ganz unverbindlich und ohne vollständige Bewerbungsunterlagen.</p>

    <div class="practice-name"><span class="dot"></span>Arztpraxis Lindenhof</div>

    <address class="contact">
      <span class="email">Helga.Weißmoor@praxis-lindenhof.ch</span><br>
      Arztpraxis Lindenhof, Brunnmattweg 7,<br>
      4788 Erlenbrunn, Tel: 0620001234
    </address>
  </article>
</body>
</html>
```